Agriculture Security Company needs a business card design

We need a business card design for a new company based in Seattle calls Ferncrest Guardline LLC. We provide high-end physical security solutions that is geared and focused towards to the marijuana grow operations, wholesalers and distributors. We DO NOT get involved in the retail operations (store fronts). We would like to see designs that incorporate professionalism, reliability, trustworthy and forward thinking as traits of our organization.

Industry/Entity Type

Security

```html
<!DOCTYPE html>
<html lang="en">
<head>
<meta charset="utf-8">
<title>Ferncrest Guardline LLC – Business Card</title>
<link href="https://fonts.googleapis.com/css2?family=Open+Sans:wght@400;600;700&display=swap" rel="stylesheet">
<style>
  :root {
    --bg: #e9e4da;
    --green-dark: #177a3a;
    --green-mid: #2f9a3f;
    --green-light: #8cc63f;
    --blue: #4a90d0;
    --white: #ffffff;
    --ink: #333333;
    --shadow: rgba(0, 0, 0, 0.22);
  }
  * { box-sizing: border-box; margin: 0; padding: 0; }
  html, body {
    width: 1200px; height: 1023px; overflow: hidden;
    background: var(--bg);
    font-family: "Open Sans", Arial, sans-serif;
  }
  .card {
    position: absolute;
    width: 560px; height: 320px;
    border-radius: 4px;
    overflow: hidden;
    box-shadow: 0 10px 28px var(--shadow);
  }
  .card-front { left: 70px; top: 150px; background: var(--white); }
  .card-back {
    left: 570px; top: 553px;
    background: linear-gradient(135deg, #ffffff 0%, #ececec 100%);
  }

  /* front */
  .front-swoosh { position: absolute; inset: 0; }
  .holder { position: absolute; left: 30px; top: 30px; color: var(--white); }
  .holder-name { font-size: 24px; font-weight: 600; letter-spacing: 0.3px; }
  .holder-title { font-size: 12px; opacity: 0.9; margin-top: 2px; }
  .front-brand {
    position: absolute; left: 250px; top: 210px;
    font-size: 24px; font-weight: 700; color: var(--green-dark);
  }
  .contact {
    position: absolute; right: 26px; top: 40px;
    text-align: right; font-size: 12px; color: var(--ink); line-height: 1.5;
  }
  .contact-company { color: var(--green-mid); font-weight: 700; }
  .contact-group { margin-bottom: 16px; }
  .contact-row { display: flex; justify-content: flex-end; align-items: center; gap: 8px; }
  .contact-row svg { width: 12px; height: 12px; fill: var(--green-light); }

  /* back */
  .back-brand {
    position: absolute; left: 60px; right: 0; top: 135px;
    text-align: center; font-size: 38px; font-weight: 700; color: var(--green-dark);
  }
  .back-url {
    position: absolute; left: 26px; top: 30px;
    writing-mode: vertical-rl;
    font-size: 14px; letter-spacing: 3px; color: var(--green-mid);
  }
</style>
</head>
<body>

<section class="card card-front">
  <svg class="front-swoosh" viewBox="0 0 560 320" preserveAspectRatio="none" aria-hidden="true">
    <path d="M0 0 H300 C230 60 150 110 90 320 H0 Z" fill="var(--green-dark)"/>
    <path d="M300 0 H330 C250 70 170 130 110 320 H90 C150 110 230 60 300 0 Z" fill="var(--white)"/>
    <path d="M330 0 H345 C260 70 185 135 125 320 H110 C170 130 250 70 330 0 Z" fill="var(--green-light)"/>
    <path d="M95 320 C150 140 220 80 300 30" fill="none" stroke="var(--blue)" stroke-width="6"/>
  </svg>
  <div class="holder">
    <div class="holder-name">Dana Whitfield</div>
    <div class="holder-title">President</div>
  </div>
  <div class="front-brand">Ferncrest Guardline</div>
  <div class="contact">
    <div class="contact-group">
      <div class="contact-company">Ferncrest Guardline LLC</div>
      <div>1820 Alder Crest Ave</div>
      <div>Seattle, WA 98101</div>
    </div>
    <div class="contact-row">206-555-0147
      <svg viewBox="0 0 12 12"><path d="M2 1h2l1 3-1.5 1a7 7 0 0 0 3.5 3.5L8 7l3 1v2a1 1 0 0 1-1 1A9 9 0 0 1 1 2a1 1 0 0 1 1-1z"/></svg>
    </div>
    <div class="contact-row">info@ferncrestguardline.com
      <svg viewBox="0 0 12 12"><rect x="1" y="2.5" width="10" height="7" rx="1"/></svg>
    </div>
    <div class="contact-row">www.ferncrestguardline.com
      <svg viewBox="0 0 12 12"><circle cx="6" cy="6" r="5"/></svg>
    </div>
  </div>
</section>

<section class="card card-back">
  <div class="back-url">www.ferncrestguardline.com</div>
  <div class="back-brand">Ferncrest Guardline</div>
</section>

</body>
</html>
```